Business Card Design & Gift cards, Gift Cert, Donation Card

Retail Gift Store-in addition to Business Cards we'd like sequenced 2 sided Gift cards, Gift Certificate Cards, and Donation Cards.please see examples and email for clarificationlogos attached with examples-
Gift Card, Gift Certificate and Donation Card will all be same style just differant upper right title, with back side info as example.
business card, as example is single sided.
looking for additional ideas for layout

Industry/Entity Type

Business

Contact Information for Business Card

211 Newman St.East Tawas, MI 48730989.362.8730Office@BrewKrew.com

Requirements
Must have
• Blue as per example
• Logos provided
• like gradiant background

```html
<!DOCTYPE html>
<html lang="en">
<head>
<meta charset="utf-8">
<title>Tillow Marsh Business Card</title>
<link rel="stylesheet" href="https://fonts.googleapis.com/css2?family=Arimo:wght@400&display=swap">
<style>
  :root {
    --page-bg: #ecebe8;
    --card-top: #b7c8da;
    --card-mid: #dfe8f2;
    --card-bottom: #c9d6e4;
    --brand-purple: #6a5fba;
    --sun-yellow: #f2e82a;
    --ink: #1d1f24;
    --card-shadow: rgba(40, 50, 70, 0.28);
  }
  * { box-sizing: border-box; margin: 0; padding: 0; }
  html, body {
    width: 1200px;
    height: 892px;
    overflow: hidden;
    background: var(--page-bg);
    font-family: "Arimo", Arial, sans-serif;
  }
  .canvas {
    position: relative;
    width: 1200px;
    height: 892px;
    display: flex;
    justify-content: center;
    align-items: center;
    gap: 90px;
  }
  .card {
    position: relative;
    width: 380px;
    height: 640px;
    border-radius: 24px;
    background: linear-gradient(160deg, var(--card-top) 0%, var(--card-mid) 55%, var(--card-bottom) 100%);
    box-shadow: 0 14px 30px var(--card-shadow);
    overflow: hidden;
  }
  .brand-name {
    position: absolute;
    display: flex;
    align-items: center;
    gap: 12px;
    color: var(--brand-purple);
    font-size: 38px;
    font-weight: 400;
    letter-spacing: 1px;
    white-space: nowrap;
  }
  .brand-dot {
    width: 16px;
    height: 16px;
    border-radius: 50%;
    background: var(--sun-yellow);
    flex: none;
  }
  .card-front .brand-name { top: 52px; left: 70px; }
  .card-back .brand-name { top: 92px; left: 70px; }
  .mascot-area {
    position: absolute;
    border-radius: 50% 50% 12px 12px;
    background: linear-gradient(180deg, rgba(106, 95, 186, 0.55) 0%, rgba(106, 95, 186, 0.35) 55%, rgba(242, 232, 42, 0.75) 100%);
  }
  .card-front .mascot-area { top: 120px; left: 100px; width: 200px; height: 230px; }
  .card-back .mascot-area { top: 200px; left: 90px; width: 210px; height: 250px; }
  .contact-list {
    position: absolute;
    left: 34px;
    bottom: 118px;
    list-style: none;
    display: flex;
    flex-direction: column;
    gap: 9px;
  }
  .contact-item {
    display: flex;
    align-items: center;
    gap: 14px;
    color: var(--ink);
    font-size: 18px;
  }
  .contact-icon {
    width: 20px;
    height: 20px;
    border-radius: 3px;
    background: var(--brand-purple);
    display: flex;
    align-items: center;
    justify-content: center;
    flex: none;
  }
</style>
</head>
<body>
  <main class="canvas">
    <section class="card card-front">
      <div class="brand-name"><span class="brand-dot"></span>Tillow Marsh</div>
      <div class="mascot-area" role="img" aria-label="Illustration of a dancing figure stepping over a rising yellow sun"></div>
      <ul class="contact-list">
        <li class="contact-item">
          <span class="contact-icon">
            <svg width="14" height="14" viewBox="0 0 14 14"><path d="M3 1.5 L5 1.5 L6 4.5 L4.5 5.5 C5.3 7.2 6.8 8.7 8.5 9.5 L9.5 8 L12.5 9 L12.5 11 C12.5 12 11.5 12.5 10.5 12.5 C5.5 12 2 8.5 1.5 3.5 C1.5 2.5 2 1.5 3 1.5 Z" fill="#fff"/></svg>
          </span>
          989.517.4296
        </li>
        <li class="contact-item">
          <span class="contact-icon">
            <svg width="14" height="14" viewBox="0 0 14 14"><rect x="1.5" y="3" width="11" height="8" fill="none" stroke="#fff" stroke-width="1.4"/><path d="M1.5 3 L7 7.5 L12.5 3" fill="none" stroke="#fff" stroke-width="1.4"/></svg>
          </span>
          Office@TillowMarsh.com
        </li>
        <li class="contact-item">
          <span class="contact-icon">
            <svg width="14" height="14" viewBox="0 0 14 14"><path d="M7 13 C4 9 3 7.5 3 5.5 A4 4 0 0 1 11 5.5 C11 7.5 10 9 7 13 Z" fill="#fff"/><circle cx="7" cy="5.5" r="1.5" fill="#6a5fba"/></svg>
          </span>
          482 Larkfield Ave. Harlow Bay, MI 48731
        </li>
      </ul>
    </section>
    <section class="card card-back">
      <div class="brand-name"><span class="brand-dot"></span>Tillow Marsh</div>
      <div class="mascot-area" role="img" aria-label="Illustration of a dancing figure stepping over a rising yellow sun"></div>
    </section>
  </main>
</body>
</html>
```